Commercial, Public Works, Contractor needs a modern web design

We are a General and Engineering contracting firm with vast experience in our industry. Our focus is on Commercial, Tenant Improvement, Restaurants, and Public Works. We are opening a new business and would like that excitement and energy to show through the new web design. The colors we like are black, red and grey, we are open to color ideas. Attached is our logo design.

Industry/Entity Type

Restaurant

```html
<!DOCTYPE html>
<html lang="en">
<head>
<meta charset="utf-8">
<title>Northgate Builders, Inc. — General Engineering Contractor</title>
<link href="https://fonts.googleapis.com/css2?family=Raleway:wght@400;500;600;700;800;900&display=swap" rel="stylesheet">
<style>
:root{
  --red:#c8101e;
  --red-dark:#a50c17;
  --black:#111;
  --ink:#2b2b2b;
  --grey-text:#8a8a8a;
  --strip:#efefef;
  --footer-outer:#1c1c1c;
  --footer-inner:#0f0f0f;
  --white:#fff;
}
*{margin:0;padding:0;box-sizing:border-box}
html,body{width:945px;height:1200px;overflow:hidden}
body{position:relative;background:var(--white);font-family:"Raleway",sans-serif;color:var(--ink)}
.abs{position:absolute}
.top-rule{left:0;top:0;width:945px;height:3px;background:var(--red)}
.brand{left:128px;top:34px;display:flex;align-items:center;gap:6px;font-weight:800;font-size:15px;color:var(--red);letter-spacing:.2px}
.brand .mark{width:14px;height:14px;background:var(--red);border-radius:50%}
.brand small{display:block}
.call{right:128px;top:20px;font-size:9px;color:var(--ink);display:flex;align-items:center;gap:4px}
.call b{color:var(--red);font-size:11px;font-weight:800}
.search{left:616px;top:50px;width:202px;height:30px;border:1px solid #ddd;display:flex}
.search span{flex:1;font-size:8.5px;color:#999;padding:10px 10px}
.search i{width:26px;background:var(--red);display:flex;align-items:center;justify-content:center}
.nav{left:127px;top:98px;width:691px;height:35px;background:var(--red);display:flex;font-size:9px;font-weight:600;color:var(--white)}
.nav a{display:flex;align-items:center;justify-content:center;height:100%;padding:0 0}
.nav .active{background:var(--black)}
.hero{left:0;top:133px;width:945px;height:400px;background:linear-gradient(90deg,#4d4d4b,#777672 40%,#5d5c59)}
.hero-photo{left:127px;top:133px;width:691px;height:400px;background:radial-gradient(ellipse at 60% 40%,#9d9c97,#6b6a66 70%,#55544f);box-shadow:0 0 12px rgba(0,0,0,.4)}
.hero-copy{left:478px;top:176px;color:var(--white)}
.hero-copy .l1{font-size:20px;font-weight:400;letter-spacing:.5px}
.hero-copy .l2{font-size:21px;font-weight:800;margin-top:4px}
.hero-copy .l3{font-size:30px;font-weight:900;margin-top:0;line-height:1.05}
.hero-copy .l3 span{color:#1a1a1a}
.arrow{top:309px;width:39px;height:50px;background:rgba(30,30,30,.75);display:flex;align-items:center;justify-content:center}
.strip{left:0;top:533px;width:945px;height:214px;background:var(--strip);border-bottom:1px solid #ddd}
.card{top:562px;width:158px;height:157px;background:var(--white);border:1px solid #ddd;padding:2px}
.card .pic{width:100%;height:121px}
.card .bar{height:31px;background:var(--black);display:flex;align-items:center;justify-content:space-between;padding:0 8px 0 6px;color:var(--white);font-size:10px;font-weight:700}
.h2{font-size:16px;font-weight:800;color:#222}
.h2 em{font-style:normal;color:var(--red)}
.welcome-pic{left:127px;top:825px;width:128px;height:113px;border:1px solid #ddd;padding:2px}
.welcome-pic div{width:100%;height:100%;background:linear-gradient(135deg,#c9a98a,#6d8aa8 60%,#e7e2d8)}
.copy{font-size:8.8px;line-height:13.6px;color:var(--grey-text)}
.news{left:518px;width:300px;display:flex}
.news .date{width:38px;border-right:1px solid #ccc;margin-right:10px;text-align:left}
.news .date b{display:block;font-size:23px;font-weight:800;line-height:24px;color:#333}
.news .date span{font-size:13px;font-weight:800;color:#333}
.news h3{font-size:10px;font-weight:500;color:var(--red);margin:-2px 0 5px}
.footer{left:0;top:985px;width:945px;height:215px;background:var(--footer-outer)}
.footer-panel{left:127px;top:985px;width:691px;height:212px;background:var(--footer-inner)}
.fcol{top:1014px;color:var(--white)}
.fcol h4{font-size:12.5px;font-weight:500;margin-bottom:10px}
.fcol p{font-size:8px;line-height:13px;color:#555}
.divider{top:1018px;width:1px;height:110px;background:#2a2a2a}
.email{width:173px;height:21px;background:var(--white);border-radius:2px;font-size:8px;color:#555;padding:6px 6px;margin-top:11px}
.btn{display:inline-block;margin-top:11px;width:71px;height:26px;background:var(--red);border-radius:2px;font-size:9px;font-weight:700;text-align:center;line-height:26px;border-bottom:2px solid var(--red-dark)}
.phone{font-size:12.5px;color:var(--red);font-weight:500;margin-top:8px}
.phone small{font-size:8px;color:var(--white);font-weight:700}
.mail{font-size:8.5px;font-weight:600}
.socials{display:flex;gap:5px;margin-top:19px}
.socials i{width:20px;height:20px;border-radius:2px}
.links{list-style:none;font-size:8.5px;line-height:15.4px;color:#9a9a9a}
.foot-rule{left:127px;top:1153px;width:691px;height:1px;background:#222}
.copyright{left:127px;top:1170px;width:691px;text-align:center;font-size:7.8px;color:#aaa}
.bottom-rule{left:0;top:1197px;width:945px;height:3px;background:var(--red)}
</style>
</head>
<body>
<div class="abs top-rule"></div>

<div class="abs brand"><span class="mark"></span><span>NORTHGATE BUILDERS, INC.</span></div>

<div class="abs call">
  <svg width="13" height="10" viewBox="0 0 13 10"><path d="M1 3c0-2 11-2 11 0v1H9V3H4v1H1z" fill="#222"/><rect x="3" y="5" width="7" height="5" rx="1" fill="#222"/></svg>
  CALL US <b>000 - 000 - 000</b>
</div>

<div class="abs search">
  <span>Enter keyword...</span>
  <i><svg width="10" height="10" viewBox="0 0 10 10"><circle cx="6" cy="4" r="2.6" fill="none" stroke="#fff" stroke-width="1.4"/><path d="M4 6L1 9" stroke="#fff" stroke-width="1.6"/></svg></i>
</div>

<nav class="abs nav">
  <a class="active" style="width:66px">HOME</a>
  <a style="width:104px">ABOUT US</a>
  <a style="width:78px">SERVICES</a>
  <a style="width:86px">PROJECTS</a>
  <a style="width:100px">OUR CLIENTS</a>
  <a style="width:72px">NEWS</a>
  <a style="width:90px">SUPPORT</a>
  <a style="width:95px">CONTACT US</a>
</nav>

<div class="abs hero" role="img" aria-label="Concrete wall with sketched city skyline"></div>
<div class="abs hero-photo" role="img" aria-label="Engineer in a suit holding a hard hat, drawing a city skyline on a concrete wall"></div>
<div class="abs hero-copy">
  <div class="l1">WE ARE A</div>
  <div class="l2">GENERAL ENGINEERING</div>
  <div class="l3"><span>CONTRACTING</span> FIRM</div>
</div>
<div class="abs arrow" style="left:0"><svg width="14" height="26" viewBox="0 0 14 26"><path d="M12 1L2 13l10 12" fill="none" stroke="#fff" stroke-width="2"/></svg></div>
<div class="abs arrow" style="left:908px;width:37px"><svg width="14" height="26" viewBox="0 0 14 26"><path d="M2 1l10 12L2 25" fill="none" stroke="#fff" stroke-width="2"/></svg></div>

<div class="abs strip"></div>
<div class="abs card" style="left:127px"><div class="pic" role="img" aria-label="Bright modern office lobby" style="background:linear-gradient(180deg,#d9dde8,#7f8db5 55%,#4a4f60)"></div><div class="bar">COMMERCIAL<svg width="8" height="10" viewBox="0 0 8 10"><path d="M1 1l5 4-5 4" fill="none" stroke="#fff" stroke-width="2"/></svg></div></div>
<div class="abs card" style="left:306px"><div class="pic" role="img" aria-label="Modern glass office buildings" style="background:linear-gradient(180deg,#4d7bb5,#b5c4d6 50%,#3f4a40)"></div><div class="bar">TENANT IMPROVEMENT<svg width="8" height="10" viewBox="0 0 8 10"><path d="M1 1l5 4-5 4" fill="none" stroke="#fff" stroke-width="2"/></svg></div></div>
<div class="abs card" style="left:484px"><div class="pic" role="img" aria-label="Restaurant terrace with pool at dusk" style="background:linear-gradient(180deg,#1d4aa0,#8c7a52 55%,#1d3d4f)"></div><div class="bar">RESTAURANTS<svg width="8" height="10" viewBox="0 0 8 10"><path d="M1 1l5 4-5 4" fill="none" stroke="#fff" stroke-width="2"/></svg></div></div>
<div class="abs card" style="left:658px"><div class="pic" role="img" aria-label="Loader and excavator on a city construction site" style="background:linear-gradient(180deg,#cfd3d4,#a89a82 60%,#6c6257)"></div><div class="bar">PUBLIC WORKS<svg width="8" height="10" viewBox="0 0 8 10"><path d="M1 1l5 4-5 4" fill="none" stroke="#fff" stroke-width="2"/></svg></div></div>

<h2 class="abs h2" style="left:128px;top:787px">WELCOME TO <em>OUR COMPANY!</em></h2>
<div class="abs welcome-pic"><div role="img" aria-label="Two workers in hard hats reviewing building plans"></div></div>
<p class="abs copy" style="left:277px;top:835px;width:200px">Lorem ipsum dolor sit amet, consec adipiscing elit, sed diam nonummy euismod tincidu nt ut laoreet dolore magna.</p>
<p class="abs copy" style="left:277px;top:890px;width:200px">Lorem ipsum dolor sit amet, consec adipiscing elit, sed diam nonummy euismod tincidu nt ut laoreet dolore magna.</p>

<h2 class="abs h2" style="left:518px;top:787px">LATEST <em>NEWS</em></h2>
<div class="abs news" style="top:824px">
  <div class="date"><b>03</b><span>FEB</span></div>
  <div><h3>Claritas est etiam proce dynamicus, qui sequitu.</h3><p class="copy">Lorem ipsum dolor sit amet, consec adipiscing elit, sed diam nonummy euismod tincidu nt ut laoreet dolore magna.</p></div>
</div>
<div class="abs news" style="top:898px">
  <div class="date"><b>03</b><span>FEB</span></div>
  <div><h3>Claritas est etiam proce dynamicus, qui sequitu.</h3><p class="copy">Lorem ipsum dolor sit amet, consec adipiscing elit, sed diam nonummy euismod tincidu nt ut laoreet dolore magna euim od tincidu nt ut laoreet dolore .</p></div>
</div>

<footer>
<div class="abs footer"></div>
<div class="abs footer-panel"></div>
<div class="abs fcol" style="left:163px;width:180px">
  <h4>Sign Up Newsletter</h4>
  <p>Lorem ipsum dolor sit amet, consectetur adipisicing elit, sed do ei.</p>
  <div class="email">Email:</div>
  <div class="btn">SIGN UP</div>
</div>
<div class="abs divider" style="left:382px"></div>
<div class="abs fcol" style="left:440px;width:200px">
  <h4>Questions Or Assustance?</h4>
  <p>Feel free to contact us at:</p>
  <div class="phone">1-800-555-0142 <small>or</small></div>
  <div class="mail">info@northgatebuilders.com</div>
  <div class="socials">
    <i style="background:#3b5ba5" role="img" aria-label="Social profile"></i>
    <i style="background:#1f9ee8" role="img" aria-label="Social profile"></i>
    <i style="background:#d7362a" role="img" aria-label="Social profile"></i>
    <i style="background:#f08b16" role="img" aria-label="News feed"></i>
    <i style="background:#cf1c34" role="img" aria-label="Social profile"></i>
    <i style="background:#1274b0" role="img" aria-label="Social profile"></i>
    <i style="background:#e0282b" role="img" aria-label="Video channel"></i>
  </div>
</div>
<div class="abs divider" style="left:648px"></div>
<div class="abs fcol" style="left:688px;width:110px">
  <h4>Information</h4>
  <ul class="links"><li>Home</li><li>About Us</li><li>Services</li><li>Projects</li><li>Gallery</li><li>Contact Us</li></ul>
</div>
<div class="abs foot-rule"></div>
<div class="abs copyright">© 2015. All Rights Reserved. Northgate General Engineering contracting</div>
<div class="abs bottom-rule"></div>
</footer>
</body>
</html>
```